IT company developing solutions for air cargo industry is looking for a new website

We are a professional IT company developing solutions for air cargo industry worldwide.

We are looking to update and completely redesign our current webpages: https://www.brisklane.cz/

What we like about our current pages are the animated graphics on the home page. These could stay, but not a must.

The design of the new pages should be very modern, clean, unique, creative, professional, and to make a statement. We are looking for animated graphics, cool and interesting interactions, cascading layers, etc.

Our company logo is yellow, gray and black. You don’t necessarily have to stick to this colour scheme, however the corporate colors should work well with the overal design of the web pages.
Dark mode pages are also an option.

The scope of the project would include creating a:

• Header
• Footer
• Landing page
• Navigation bar (8 tabs)
• Subpages (10)

In the first stage we are looking only for the header / footer / landing page with navigaton bar / Solutions page design.
As a second round, finalists might be asked to submit another section of the website to see their consistency in terms of the look and feel proposed for the Homepage and Solutions’ pages.
The winning designer will then complete the rest of the pages.

Attached you will find a brief for the first scope of the project. Please read the note section on slide nr. 3 carefully to understand, what we exactly are looking for to achieve.

Industry/Entity Type

Aviation

Number of Pages Required

1 page

Requirements
Must have
• See brief
Nice to have
• See brief
Should not have
• See brief

```html
<!DOCTYPE html>
<html lang="en">
<head>
<meta charset="utf-8">
<title>Brisk Lane — Air Cargo IT Solutions</title>
<link rel="stylesheet" href="https://fonts.googleapis.com/css2?family=Roboto:wght@400;500;700&display=swap">
<style>
:root{
  --yellow:#fdc91b;
  --dark:#282828;
  --ink:#2a2a2a;
  --nav-ink:#3a3a3a;
  --hero-bg:#f2f2f4;
  --white:#ffffff;
  --globe-light:#1fd8ff;
  --globe-mid:#0a78e0;
  --globe-deep:#062a78;
}
*{box-sizing:border-box;margin:0;padding:0}
html,body{width:1200px;height:1152px;overflow:hidden}
body{font-family:"Roboto",Arial,sans-serif;color:var(--ink);background:var(--white)}
.announcement{height:51px;background:var(--yellow);display:flex;align-items:center;justify-content:center;font-size:13.7px;font-weight:500;color:#222}
.site-header{height:86px;display:flex;align-items:center;padding:0 111px;background:var(--white)}
.brand{display:flex;align-items:center;gap:22px;text-decoration:none}
.brand-mark{width:48px;height:48px;background:var(--yellow)}
.brand-name{font-size:28px;font-weight:500;color:#4a4a4a}
.main-nav{margin-left:auto;display:flex;gap:27px;list-style:none}
.main-nav a{font-size:13.7px;color:var(--nav-ink);text-decoration:none;display:flex;align-items:center;gap:3px}
.caret{width:0;height:0;border-left:4px solid transparent;border-right:4px solid transparent;border-top:5px solid var(--nav-ink)}
.hero{position:relative;height:586px;background:radial-gradient(circle at 30% 40%,#f7f7f9,var(--hero-bg))}
.hero-title{position:absolute;left:111px;top:160px;font-size:41px;font-weight:700;line-height:59px;color:var(--ink)}
.btn-learn{position:absolute;left:111px;top:372px;width:143px;height:58px;border-radius:29px;background:var(--yellow);display:flex;align-items:center;justify-content:center;font-size:15.5px;font-weight:500;color:#222;text-decoration:none}
.globe{position:absolute;left:643px;top:73px;width:438px;height:438px;border-radius:50%;background:radial-gradient(circle at 55% 20%,var(--globe-light),var(--globe-mid) 45%,var(--globe-deep) 95%)}
.stats{height:348px;background:var(--dark);color:var(--white);text-align:center;padding-top:52px}
.stats-lead{font-size:22px;font-weight:700;line-height:31.5px}
.stat-list{display:flex;justify-content:center;gap:54px;list-style:none;margin-top:31px}
.stat{width:115px;display:flex;flex-direction:column;align-items:center}
.stat-ring{width:115px;height:115px;border:1.5px solid var(--yellow);border-radius:50%;display:flex;align-items:center;justify-content:center;font-size:17.5px;font-weight:500}
.stat-label{margin-top:11px;font-size:12.5px;line-height:18px;width:140px}
.site-footer{height:81px;background:var(--yellow);display:flex;align-items:center;justify-content:center;font-size:15.5px;color:#333;gap:14px}
</style>
</head>
<body>
<div class="announcement">Affordable IT Solutions That Revolutionize Tomorrow's Air Cargo Today</div>
<header class="site-header">
  <a class="brand" href="https://www.brisklane.cz/"><span class="brand-mark"></span><span class="brand-name">Brisk Lane</span></a>
  <ul class="main-nav">
    <li><a href="#">Industries</a></li>
    <li><a href="#">Solutions <span class="caret"></span></a></li>
    <li><a href="#">Operational Support</a></li>
    <li><a href="#">Case Studies</a></li>
    <li><a href="#">Testimonials</a></li>
    <li><a href="#">News</a></li>
    <li><a href="#">About Us <span class="caret"></span></a></li>
  </ul>
</header>
<section class="hero">
  <h1 class="hero-title">Seamlessly connecting<br>the air cargo industry<br>from Manila to Tahiti</h1>
  <a class="btn-learn" href="#">LEARN MORE</a>
  <div class="globe" role="img" aria-label="Glowing blue globe with location pins and a flight route across Europe and Asia"></div>
</section>
<section class="stats">
  <p class="stats-lead">We are not IT tech experts attempting to do cargo! We are cargo<br>experts with programming skills!</p>
  <ul class="stat-list">
    <li class="stat"><span class="stat-ring">2014</span><span class="stat-label">Established</span></li>
    <li class="stat"><span class="stat-ring">22</span><span class="stat-label">Employees</span></li>
    <li class="stat"><span class="stat-ring">11,500,000 +</span><span class="stat-label">Nr. of Annual Electronic Exchanges</span></li>
    <li class="stat"><span class="stat-ring">18</span><span class="stat-label">Countries covered</span></li>
    <li class="stat"><span class="stat-ring">20+</span><span class="stat-label">Connected Clients</span></li>
    <li class="stat"><span class="stat-ring">350,000 +</span><span class="stat-label">Nr. of Annual AWBs</span></li>
  </ul>
</section>
<footer class="site-footer"><span>©Copyrights 2024 Brisklane</span><span>|</span><span>All Rights Reserved</span></footer>
</body>
</html>
```